Brintel Works - Fast, Efficient and Gas Mainteance for Domestic, Commercial and Industrial clients

We are in the process of purchasing a new business and would like to get a new logo and business card.
Business is a gas maintenance business that also does new gas installations.
Has been established since 1988.
Services include:
Install all types of gas appliances & equipment inc. hot water units
Maintain / repair / replace all types of gas appliances & equipment

Target Market(s)

Domestic, Commercial and Industrial clients

Industry/Entity Type

Business

Contact Information for Business Card

admin@brintelworks.com.au
07 3918 4726
Brintel Works PTY LTD

Logo Text

Gas Fitting & Plumbing Maintenance Specialists

Font styles to use
Sans Serif

Requirements
Must have
• Logo
• Business name, contact number, email address, web address
• Domestic | Commercial | Industrial Est Since 1988
Nice to have
• Possibly a black card with a flame logo to one side
Should not have
• Spelling errors

```html
<!DOCTYPE html>
<html lang="en">
<head>
<meta charset="utf-8">
<title>Brintel Works – Business Card</title>
<link rel="stylesheet" href="https://fonts.googleapis.com/css2?family=Montserrat:wght@600&family=Cinzel:wght@400&family=Open+Sans:wght@400&display=swap">
<style>
  :root {
    --backdrop: #2e2824;
    --card: #161616;
    --card-edge: #222;
    --gold: #f2c01e;
    --bronze: #a8683a;
    --ink: #e9e6e1;
    --divider: #4a3a2c;
    --flame-deep: #b8400c;
    --flame-mid: #ef8a1c;
    --flame-light: #ffc552;
  }
  * { box-sizing: border-box; margin: 0; padding: 0; }
  html, body { width: 1200px; height: 844px; overflow: hidden; }
  body {
    background: var(--backdrop);
    font-family: "Open Sans", Arial, sans-serif;
    color: var(--ink);
    position: relative;
  }
  .card {
    position: absolute;
    top: 272px;
    width: 520px;
    height: 300px;
    background: var(--card);
    border: 1px solid var(--card-edge);
    box-shadow: 0 10px 30px rgba(0,0,0,.45);
    overflow: hidden;
  }
  .card--contact { left: 50px; }
  .card--cover { left: 630px; }

  /* contact side */
  .brand {
    position: absolute;
    left: 34px;
    top: 90px;
    width: 200px;
    text-align: center;
  }
  .brand-mark {
    display: block;
    width: 46px;
    height: 46px;
    margin: 0 auto 14px;
    border-radius: 50%;
    background: var(--flame-mid);
  }
  .brand-name {
    font-family: "Montserrat", Arial, sans-serif;
    font-weight: 600;
    font-size: 24px;
    letter-spacing: 1px;
    color: var(--gold);
    line-height: 1;
  }
  .brand-sub {
    font-family: "Cinzel", Georgia, serif;
    font-size: 12px;
    letter-spacing: 3px;
    color: var(--bronze);
    margin-top: 6px;
  }
  .divider {
    position: absolute;
    left: 262px;
    top: 60px;
    width: 1px;
    height: 130px;
    background: var(--divider);
  }
  .contact {
    position: absolute;
    left: 284px;
    top: 58px;
    font-size: 12.5px;
    line-height: 1.45;
  }
  .address { margin-bottom: 22px; }
  .contact-list { list-style: none; }
  .contact-list li { display: flex; align-items: center; gap: 9px; }
  .contact-list svg { width: 11px; height: 11px; flex: none; }
  .tagline {
    position: absolute;
    left: 34px;
    bottom: 34px;
    font-size: 14px;
    letter-spacing: .2px;
  }

  /* cover side */
  .cover-brand {
    position: absolute;
    right: 34px;
    top: 36px;
    text-align: right;
  }
  .cover-brand .brand-name { font-size: 34px; }
  .cover-brand .brand-sub { font-size: 14px; letter-spacing: 4px; margin-top: 8px; }
  .flames {
    position: absolute;
    left: 0;
    right: 0;
    bottom: 0;
    height: 175px;
    background:
      radial-gradient(ellipse 30% 70% at 82% 90%, var(--flame-light), transparent 70%),
      radial-gradient(ellipse 38% 65% at 40% 100%, var(--flame-mid), transparent 72%),
      linear-gradient(to top, var(--flame-deep) 0%, rgba(184,64,12,.55) 45%, rgba(22,22,22,0) 100%);
  }
</style>
</head>
<body>

<section class="card card--contact">
  <div class="brand">
    <span class="brand-mark"></span>
    <div class="brand-name">BRINTEL WORKS</div>
    <div class="brand-sub">PTY LTD</div>
  </div>

  <div class="divider"></div>

  <div class="contact">
    <p class="address">12345, Address Goes Here<br>Country Name, 123456.</p>
    <ul class="contact-list">
      <li>
        <svg viewBox="0 0 12 12" aria-hidden="true"><path d="M2.5 1 L4.5 1 L5 3.5 L3.8 4.4 Q4.8 6.9 7.6 8.2 L8.5 7 L11 7.5 L11 9.5 Q10.5 11 9 11 Q1 10 1 2.5 Q1 1 2.5 1Z" fill="var(--flame-mid)"/></svg>
        07 3918 4726
      </li>
      <li>
        <svg viewBox="0 0 12 12" aria-hidden="true"><rect x="1" y="2.5" width="10" height="7" fill="var(--flame-mid)"/><path d="M1 2.5 L6 6.5 L11 2.5" stroke="var(--card)" fill="none" stroke-width="1"/></svg>
        admin@brintelworks.com.au
      </li>
      <li>
        <svg viewBox="0 0 12 12" aria-hidden="true"><circle cx="6" cy="6" r="5" fill="var(--flame-mid)"/><path d="M1 6 H11 M6 1 V11 M3 3.2 Q6 5 9 3.2 M3 8.8 Q6 7 9 8.8" stroke="var(--card)" stroke-width=".8" fill="none"/></svg>
        www.brintelworks.com.au
      </li>
    </ul>
  </div>

  <p class="tagline">Domestic | Commercial | Industrial Est Since 1988</p>
</section>

<section class="card card--cover">
  <div class="cover-brand">
    <div class="brand-name">BRINTEL WORKS</div>
    <div class="brand-sub">PTY LTD</div>
  </div>
  <div class="flames" role="img" aria-label="Photograph of orange gas flames rising along the bottom of the card"></div>
</section>

</body>
</html>
```